Trade Show booth design

I need the following designs for my trade booth:
1. backboard design 3m Wx2mH
2. Tressle table, tablecloth front panel design 1800W x 740mmH
3. Pop-up banner. I have included our logos and some design content ideas:
Headline:
"Cleaner Classrooms. Safer Schools."
Subheadline:
"Specialist Cleaning Solutions for Education Facilities"
Key Points to Grab Attention:
Healthy Environments: Create hygienic, safe learning spaces for students and staff with our expert cleaning services.
Tailored to Your Needs: Custom cleaning plans for classrooms, labs, libraries, and sports facilities.
Affordable Excellence: Premium results without premium costs – tailored plans mean you only pay for what you need.
Safety First: All staff are trained, highly vetted, and hold current Working with Children Checks (WWCC).
Eco-Conscious Cleaning: Using non-toxic, eco-friendly products certified for health and safety.
What Schools Really Need:
Reliability: Consistent, high-quality cleaning from a trusted provider.
Cost-Effectiveness: Solutions that fit tight budgets while maintaining high standards.
Expertise: Over 30 years of experience in education facility cleaning.
Disinfection Services: Focus on high-touch areas to reduce the spread of germs and ensure peace of mind.
Visual Elements:
Images of bright, clean classrooms, a happy teacher welcoming students, or students collaborating in a spotless library.
Icons representing safety (shield), hygiene (sparkling star), and eco-friendliness (leaf).
Your logo with the tagline: "Trusted by Queensland Schools Since 1995."
Call-to-Action:
"Visit us to discuss your school’s cleaning needs and book a FREE consultation."
Include contact details: Phone: 1300 594 316 | Website: www.brightmorefacility.com.au
Target Market(s)
Education sector
Industry/Entity Type
Commercial Cleaning
Font styles to use
Other font styles liked:
- Montserrat
Look and feel

```html
<!DOCTYPE html>
<html lang="en">
<head>
<meta charset="utf-8">
<title>Brightmore Facility – Pop-up Banner</title>
<link rel="stylesheet" href="https://fonts.googleapis.com/css2?family=Montserrat:wght@300;400;500;600;700;800&display=swap">
<style>
  :root{
    --navy:#0b2442;
    --navy-mid:#0f3458;
    --navy-ink:#0d2a4a;
    --cyan:#1ec8f5;
    --cyan-pill:#2cc3f1;
    --white:#ffffff;
  }
  *{box-sizing:border-box;margin:0;padding:0}
  html,body{width:1200px;height:2320px;overflow:hidden;background:var(--navy)}
  .banner{
    position:relative;width:1200px;height:2320px;overflow:hidden;
    font-family:"Montserrat",sans-serif;color:var(--white);
    background:radial-gradient(ellipse at 70% 45%, var(--navy-mid) 0%, var(--navy) 65%);
  }
  .brand{
    position:absolute;top:112px;left:0;width:100%;height:76px;
    display:flex;justify-content:center;align-items:center;gap:22px;
  }
  .brand-dot{width:34px;height:34px;border-radius:50%;background:var(--white)}
  .brand-name{font-size:64px;font-weight:700;letter-spacing:2px;line-height:1;color:var(--white)}
  .tagline{
    position:absolute;top:256px;width:100%;text-align:center;
    font-size:27px;font-weight:600;letter-spacing:2.5px;line-height:1;
  }
  .tagline .accent{color:var(--cyan)}
  .headline{position:absolute;top:0;left:0;width:100%;height:0;text-align:center}
  .headline span{position:absolute;left:0;width:100%;line-height:1;white-space:nowrap}
  .headline .line-light{top:346px;font-size:92px;font-weight:300;color:var(--cyan);letter-spacing:2px}
  .headline .line-white{top:424px;font-size:112px;font-weight:800;letter-spacing:-1px}
  .headline .line-cyan{top:524px;font-size:100px;font-weight:800;color:var(--cyan);letter-spacing:-1px}
  .dots{position:absolute;top:636px;left:0;width:100%;display:flex;justify-content:center;gap:9px}
  .dots span{width:12px;height:12px;border-radius:50%;background:var(--white)}
  .subheadline{
    position:absolute;top:673px;width:100%;text-align:center;
    font-size:44px;font-weight:600;line-height:52px;
  }
  .points{position:absolute;top:876px;left:115px;width:840px}
  .point{
    height:168px;margin-bottom:16px;border-radius:84px 0 0 84px;
    background:linear-gradient(90deg,var(--cyan-pill),#45cdf4);
    display:flex;align-items:center;color:var(--navy-ink);
  }
  .point-icon{width:160px;display:flex;justify-content:center;padding-left:10px}
  .point-icon svg{width:64px;height:64px}
  .point-divider{width:3px;height:110px;background:var(--navy-ink)}
  .point-text{padding-left:26px;font-size:35px;font-weight:600;line-height:42px}
  .photo-cleaner{
    position:absolute;left:830px;top:816px;width:260px;height:645px;border-radius:120px 120px 30px 30px;
    background:linear-gradient(180deg,#8fb8cf 0%,#34407a 45%,#2a4d78 75%,#e9edf0 100%);
  }
  .classroom{position:absolute;left:0;top:1488px;width:1200px;height:832px}
  .cta{
    position:absolute;left:0;top:1959px;width:1200px;height:298px;background:var(--cyan);
    color:var(--navy-ink);text-align:center;
  }
  .cta-lead{margin-top:22px;font-size:34px;font-weight:500;line-height:42px}
  .cta-pill{
    margin:14px auto 0;width:965px;height:58px;border-radius:29px;overflow:hidden;
    display:flex;background:var(--navy-ink);font-size:44px;font-weight:800;letter-spacing:1.5px;
  }
  .cta-pill .book{width:273px;background:var(--white);color:var(--navy-ink);line-height:58px;border-radius:29px 0 0 29px}
  .cta-pill .consult{flex:1;color:var(--white);line-height:58px;text-align:left;padding-left:30px}
  .cta-pill .free{color:var(--cyan)}
  .cta-phone{
    margin-top:8px;display:flex;justify-content:center;align-items:center;gap:14px;
    font-size:90px;font-weight:700;line-height:96px;letter-spacing:-1px;
  }
  .cta-phone svg{width:64px;height:64px}
  .cta-web{font-size:44px;font-weight:700;letter-spacing:6px;line-height:50px}
</style>
</head>
<body>
<main class="banner">
  <header class="brand">
    <span class="brand-dot"></span>
    <span class="brand-name">BRIGHTMORE FACILITY</span>
  </header>

  <p class="tagline">TRUSTED BY QUEENSLAND SCHOOLS <span class="accent">SINCE 1995</span></p>

  <h1 class="headline">
    <span class="line-light">CLEANER</span>
    <span class="line-white">CLASSROOMS</span>
    <span class="line-cyan">SAFER SCHOOLS</span>
  </h1>

  <div class="dots"><span></span><span></span><span></span><span></span><span></span></div>

  <p class="subheadline">Specialist Cleaning Solutions for<br>Education Facilities</p>

  <section class="points">
    <div class="point">
      <div class="point-icon">
        <svg viewBox="0 0 64 64" fill="#0d2a4a">
          <polygon points="32,2 35,10 43,10 37,15 39,23 32,18 25,23 27,15 21,10 29,10"/>
          <circle cx="32" cy="32" r="7"/><path d="M20 60v-10a12 10 0 0 1 24 0v10z"/>
          <circle cx="12" cy="36" r="5"/><path d="M2 58v-8a10 8 0 0 1 18 0v8z"/>
          <circle cx="52" cy="36" r="5"/><path d="M44 58v-8a10 8 0 0 1 18 0v8z"/>
        </svg>
      </div>
      <span class="point-divider"></span>
      <p class="point-text">Over 30 years of<br>expertise in<br>commercial cleaning.</p>
    </div>
    <div class="point">
      <div class="point-icon">
        <svg viewBox="0 0 64 64" fill="#0d2a4a">
          <path d="M32 58 6 32A14 14 0 0 1 32 14 14 14 0 0 1 58 32z"/>
          <path d="M22 40l10-10 8 8M28 44l8-8M34 48l6-6" stroke="#2cc3f1" stroke-width="3" fill="none"/>
        </svg>
      </div>
      <span class="point-divider"></span>
      <p class="point-text">Trusted by schools,<br>universities, and TAFEs<br>across Queensland.</p>
    </div>
    <div class="point">
      <div class="point-icon">
        <svg viewBox="0 0 64 64" fill="#0d2a4a">
          <path d="M32 4c10 4 14 12 10 20-6-2-12-8-10-20z"/>
          <path d="M6 44c2-10 10-16 18-14 0 8-8 14-18 14z"/>
          <path d="M58 44c-10 2-18-2-20-10 8-4 16 0 20 10z"/>
          <path d="M20 22a18 18 0 0 0-6 14M44 56a18 18 0 0 1-20 0M50 24a18 18 0 0 1 2 10" stroke="#0d2a4a" stroke-width="3" fill="none"/>
        </svg>
      </div>
      <span class="point-divider"></span>
      <p class="point-text">100% Carbon Neutral<br>and Eco-Certified<br>Services.</p>
    </div>
  </section>

  <div class="photo-cleaner" role="img" aria-label="Photo of a smiling cleaner in an apron and orange gloves mopping the floor"></div>

  <svg class="classroom" viewBox="0 0 1200 832" preserveAspectRatio="none">
    <defs>
      <linearGradient id="roomTone" x1="0" y1="0" x2="0" y2="1">
        <stop offset="0" stop-color="#eef2f5"/>
        <stop offset="0.45" stop-color="#cfd8e0"/>
        <stop offset="0.75" stop-color="#b59874"/>
        <stop offset="1" stop-color="#9ea9b3"/>
      </linearGradient>
    </defs>
    <path role="img" aria-label="Photo of a bright, clean classroom with rows of desks and a teacher standing in the aisle"
          d="M0 290 C180 120 420 20 680 10 C780 6 860 18 900 40 C940 150 1040 230 1200 270 L1200 832 L0 832 Z"
          fill="url(#roomTone)"/>
  </svg>

  <section class="cta">
    <p class="cta-lead">Visit us to discuss your school’s cleaning needs &amp;</p>
    <div class="cta-pill">
      <span class="book">BOOK A</span>
      <span class="consult"><span class="free">FREE</span> CONSULTATION</span>
    </div>
    <div class="cta-phone">
      <svg viewBox="0 0 64 64">
        <circle cx="32" cy="32" r="30" fill="#0d2a4a"/>
        <path d="M22 16c2 0 4 6 4 8s-3 3-3 5c2 5 6 9 11 11 2 0 3-3 5-3s8 2 8 4-3 7-8 7C27 48 16 37 16 23c0-5 4-7 6-7z" fill="#1ec8f5"/>
      </svg>
      <span>1300 594 316</span>
    </div>
    <p class="cta-web">www.brightmorefacility.com.au</p>
  </section>
</main>
</body>
</html>
```